Facebook Header Design Project.

I'm supplying white and colored logos. The Facebook page already exists. URL = https://www.brindlepost.example/quillarc.studio The design should not be based on what's already there. Consider mobile implications of the design. This Design will form the designs of other social media headers. QuillArc is a web design | digital marketing company.

Target Market(s)

People interested in web design | digital marketing services.

Industry/Entity Type

QuillArc is a web design | digital marketing company. That should be clear in the design.

Colors
0054AA
0677BA
7BADD7
CADEEF
E8F1F8

Requirements
Must have
• Logo. Use Facebook header image dimension.
Nice to have
• Use a color scheme like the logo and feel free to add a color or two from the other side of the color whee.

```html
<!DOCTYPE html>
<html lang="en">
<head>
<meta charset="utf-8">
<title>QuillArc – Web Design &amp; Digital Marketing Header</title>
<link rel="stylesheet" href="https://fonts.googleapis.com/css2?family=Barlow+Semi+Condensed:wght@700&family=Oswald:wght@400&family=Lato:wght@700&display=swap">
<style>
  :root {
    --navy: #0054AA;
    --blue: #0677BA;
    --sky: #7BADD7;
    --mist: #CADEEF;
    --ice: #E8F1F8;
    --white: #ffffff;
    --ink: #2354a3;
    --stage: #020a2a;
    --photo-paper: #f3f3f3;
    --photo-light: #dcdcdc;
    --photo-mid: #a9a9a9;
    --photo-dark: #3a3a3a;
  }
  * { margin: 0; padding: 0; box-sizing: border-box; }
  html, body {
    width: 1200px; height: 744px; overflow: hidden;
    background: var(--stage);
  }
  .header {
    position: absolute; left: 0; top: 150px;
    width: 1200px; height: 445px;
    background: var(--white);
    overflow: hidden;
  }
  .header__photo {
    position: absolute; left: 515px; top: 0;
    width: 685px; height: 445px;
    background:
      linear-gradient(90deg, var(--white) 0%, rgba(255,255,255,0.85) 18%, rgba(255,255,255,0) 45%),
      radial-gradient(ellipse 150px 95px at 58% 20%, var(--photo-dark) 0%, var(--photo-dark) 55%, rgba(58,58,58,0) 100%),
      radial-gradient(ellipse 130px 60px at 58% 50%, #6a6a6a 0%, rgba(106,106,106,0) 100%),
      radial-gradient(ellipse 170px 90px at 62% 100%, #8a8a8a 0%, rgba(138,138,138,0) 100%),
      linear-gradient(90deg, rgba(0,0,0,0) 0%, rgba(0,0,0,0) 84%, rgba(120,120,120,0.45) 86%, rgba(120,120,120,0.45) 100%),
      linear-gradient(160deg, var(--photo-paper) 0%, var(--photo-light) 55%, var(--photo-mid) 100%);
  }
  .header__headline-band {
    position: absolute; left: 0; top: 105px;
    width: 560px; height: 172px;
    background: linear-gradient(90deg, var(--mist) 0%, var(--ice) 30%, rgba(232,241,248,0) 100%);
  }
  .header__footer-band {
    position: absolute; left: 0; top: 350px;
    width: 780px; height: 95px;
    background: linear-gradient(90deg, var(--blue) 0%, var(--sky) 42%, rgba(202,222,239,0.6) 70%, rgba(232,241,248,0) 100%);
  }
  .brand {
    position: absolute; left: 62px; top: 32px;
    display: flex; align-items: center; gap: 10px;
    font-family: "Barlow Semi Condensed", "Arial Narrow", sans-serif;
    font-weight: 700; font-size: 48px; line-height: 1;
    color: var(--navy);
  }
  .brand__mark {
    width: 16px; height: 16px; border-radius: 50%;
    background: var(--navy);
  }
  .headline {
    position: absolute; left: 62px; top: 108px;
    font-weight: normal;
  }
  .headline__primary {
    display: block;
    font-family: "Barlow Semi Condensed", "Arial Narrow", sans-serif;
    font-weight: 700; font-size: 66px; line-height: 66px;
    letter-spacing: 2px;
    color: var(--ink);
  }
  .headline__secondary {
    display: block; margin-top: 14px;
    font-family: "Oswald", "Arial Narrow", sans-serif;
    font-weight: 400; font-size: 78px; line-height: 78px;
    letter-spacing: 0;
    color: transparent;
    -webkit-text-stroke: 2px var(--blue);
  }
  .deco-plus { position: absolute; left: 510px; top: 64px; }
  .deco-dots { position: absolute; left: 12px; top: 292px; }
  .intro {
    position: absolute; left: 61px; top: 366px;
    width: 440px;
    font-family: "Lato", "Calibri", sans-serif;
    font-weight: 700; font-size: 15px; line-height: 19px;
    letter-spacing: -0.2px;
    color: var(--white);
  }
</style>
</head>
<body>
  <section class="header">
    <div class="header__photo" role="img" aria-label="Black and white top-down photo of a person typing on a laptop at a desk with a notebook, pen, plant, book and coffee cup"></div>
    <div class="header__headline-band"></div>
    <div class="header__footer-band"></div>

    <div class="brand"><span class="brand__mark"></span>QuillArc</div>

    <svg class="deco-plus" width="60" height="52" viewBox="0 0 60 52" aria-hidden="true">
      <g stroke="#0677BA" stroke-width="2.4" stroke-linecap="round">
        <path d="M3 7h8M7 3v8M24 7h8M28 3v8M45 7h8M49 3v8"/>
        <path d="M3 27h8M7 23v8M24 27h8M28 23v8M45 27h8M49 23v8"/>
        <path d="M3 47h8M7 43v8M24 47h8M28 43v8M45 47h8M49 43v8"/>
      </g>
    </svg>

    <svg class="deco-dots" width="84" height="44" viewBox="0 0 84 44" aria-hidden="true">
      <defs>
        <pattern id="dot-grid" width="11.3" height="13" patternUnits="userSpaceOnUse">
          <circle cx="3" cy="3" r="1.6" fill="#0677BA"/>
        </pattern>
      </defs>
      <rect width="84" height="44" fill="url(#dot-grid)"/>
    </svg>

    <h1 class="headline">
      <span class="headline__primary">WEB DESIGN &amp;</span>
      <span class="headline__secondary">DIGITAL MARKETING</span>
    </h1>

    <p class="intro">Lorem Ipsum is simply dummy text of the printing and typesetting industry. Lorem has been the industry's standard dummy text ever since the 1500s</p>
  </section>
</body>
</html>
```